Business Cards - New Logo Rebranding

Hello We know have a red and blue logo and are looking to create new cards. We are looking for the best creativity of the new logo merged with some of the existing artwork provided.

Target Market(s)

Realtors

Industry/Entity Type

Real Estate

Contact Information for Business Card

New logo with rebranded colors

Requirements
Must have
• Creative use of the new logo

```html
<!DOCTYPE html>
<html lang="en">
<head>
<meta charset="utf-8">
<title>Vantage Group – Business Cards</title>
<link href="https://fonts.googleapis.com/css2?family=Montserrat:wght@400;500;600;700;800&family=Oswald:wght@500;600;700&display=swap" rel="stylesheet">
<style>
  :root {
    --brand-blue: #1674c4;
    --brand-blue-dark: #0f5ea8;
    --brand-red: #e21d2b;
    --white: #ffffff;
    --ink: #2b2b2b;
    --stage: #3a3a3a;
    --photo-top: #5d8fc9;
    --photo-bottom: #1f56a8;
    --badge-a: #c9a23a;
    --badge-b: #b9262f;
    --badge-c: #8c8c8c;
  }
  * { box-sizing: border-box; margin: 0; padding: 0; }
  html, body { width: 1200px; height: 875px; overflow: hidden; }
  body {
    background: var(--stage);
    font-family: "Montserrat", Arial, sans-serif;
    display: flex;
    align-items: center;
    justify-content: center;
    gap: 40px;
  }
  .card {
    width: 540px;
    height: 309px;
    border-radius: 18px;
    position: relative;
    overflow: hidden;
  }

  /* Back side */
  .card-back {
    background: var(--brand-blue);
    color: var(--white);
    padding: 28px 26px 0 30px;
  }
  .back-headline {
    font-weight: 800;
    font-size: 18.5px;
    line-height: 1.1;
    white-space: nowrap;
  }
  .back-subhead {
    font-family: "Oswald", Arial, sans-serif;
    font-weight: 600;
    color: var(--brand-red);
    font-size: 22px;
    line-height: 1.3;
    margin-top: 6px;
    text-transform: uppercase;
    white-space: nowrap;
  }
  .benefit-list { list-style: none; margin-top: 6px; }
  .benefit-list li {
    display: flex;
    align-items: center;
    gap: 9px;
    font-size: 13px;
    font-weight: 500;
    line-height: 20px;
    white-space: nowrap;
  }
  .benefit-bullet {
    width: 13px; height: 13px;
    border-radius: 50%;
    background: var(--white);
    flex: none;
  }
  .badge-row {
    position: absolute;
    right: 22px;
    bottom: 14px;
    display: flex;
    gap: 8px;
    align-items: center;
  }
  .badge { width: 28px; height: 28px; border-radius: 50%; border: 2px solid var(--white); }
  .badge-gold { background: var(--badge-a); }
  .badge-red { background: var(--badge-b); }
  .badge-grey { background: var(--badge-c); }
  .badge-wide { width: 44px; height: 22px; border-radius: 4px; background: var(--brand-blue-dark); border: 2px solid var(--white); }

  /* Front side */
  .card-front { background: var(--white); color: var(--ink); }
  .brand-lockup {
    position: absolute;
    left: 28px; top: 26px;
    display: flex; align-items: center; gap: 10px;
  }
  .brand-mark { width: 44px; height: 44px; border-radius: 50%; background: var(--brand-blue); }
  .brand-name {
    font-weight: 800;
    font-size: 22px;
    color: var(--brand-blue);
    line-height: 1;
  }
  .brand-tagline {
    font-size: 8px;
    font-weight: 600;
    color: var(--brand-blue);
    letter-spacing: 0.6px;
    margin-top: 4px;
  }
  .holder-name {
    position: absolute;
    left: 28px; top: 92px;
    font-family: "Oswald", Arial, sans-serif;
    font-weight: 600;
    font-size: 30px;
    color: var(--brand-red);
    letter-spacing: 0.5px;
  }
  .title-band {
    position: absolute;
    left: 0; top: 138px;
    width: 340px; height: 30px;
    background: var(--brand-blue);
    color: var(--white);
    font-size: 15px;
    font-weight: 500;
    padding: 6px 28px;
  }
  .contact-list {
    position: absolute;
    left: 28px; top: 178px;
    list-style: none;
  }
  .contact-list li {
    display: flex; align-items: center; gap: 9px;
    font-size: 13px;
    line-height: 21px;
  }
  .contact-list svg { width: 13px; height: 13px; flex: none; }
  .holder-photo {
    position: absolute;
    right: 0; top: 0;
    width: 200px; height: 271px;
    background: linear-gradient(180deg, var(--photo-top), var(--photo-bottom));
  }
  .service-strip {
    position: absolute;
    left: 0; bottom: 0;
    width: 100%; height: 38px;
    background: var(--brand-blue);
    color: var(--white);
    font-family: "Oswald", Arial, sans-serif;
    font-weight: 600;
    font-size: 16px;
    letter-spacing: 0.4px;
    display: flex; align-items: center;
    padding-left: 28px;
  }
</style>
</head>
<body>

  <section class="card card-back">
    <h2 class="back-headline">CALIFORNIA'S #1 INSPECTION COMPANY!</h2>
    <p class="back-subhead">Why choose Vantage Group...</p>
    <ul class="benefit-list">
      <li><span class="benefit-bullet"></span>Performing Inspections Since 1984</li>
      <li><span class="benefit-bullet"></span>HomeCheck Guild Certified Master / Professional Inspectors</li>
      <li><span class="benefit-bullet"></span>500,000+ Inspections Completed Statewide</li>
      <li><span class="benefit-bullet"></span>90-Day Inspection Guarantees</li>
      <li><span class="benefit-bullet"></span>Request of Repairs Pricer Report</li>
      <li><span class="benefit-bullet"></span>AeroSafe Drone Licensed Roof Inspectors upon request</li>
      <li><span class="benefit-bullet"></span>5,000+ 5-Star Reviews on ReviewHub &amp; StarList</li>
    </ul>
    <div class="badge-row" aria-label="Certification badges">
      <span class="badge badge-red"></span>
      <span class="badge-wide"></span>
      <span class="badge badge-gold"></span>
      <span class="badge badge-red"></span>
      <span class="badge badge-grey"></span>
      <span class="badge badge-gold"></span>
    </div>
  </section>

  <section class="card card-front">
    <div class="brand-lockup">
      <span class="brand-mark"></span>
      <div>
        <div class="brand-name">VANTAGE GROUP</div>
        <div class="brand-tagline">INSPECTION PROFESSIONALS</div>
      </div>
    </div>
    <div class="holder-name">DANIEL MORENO</div>
    <div class="title-band">Certified Mold Inspector</div>
    <ul class="contact-list">
      <li><svg viewBox="0 0 16 16"><path d="M3 1l3 3-1.5 2a9 9 0 005 5l2-1.5 3 3-2 2C6 14 2 10 1 3z" fill="var(--brand-red)"/></svg>800.555.0142</li>
      <li><svg viewBox="0 0 16 16"><rect x="4" y="1" width="8" height="14" rx="1.5" fill="none" stroke="var(--brand-red)" stroke-width="1.6"/><circle cx="8" cy="12.5" r="0.9" fill="var(--brand-red)"/></svg>562.555.0187</li>
      <li><svg viewBox="0 0 16 16"><rect x="1" y="3" width="14" height="10" fill="var(--brand-red)"/><path d="M1 3l7 6 7-6" fill="none" stroke="var(--white)" stroke-width="1.2"/></svg>dmoreno@vantageinspect.com</li>
      <li><svg viewBox="0 0 16 16"><circle cx="8" cy="8" r="6.5" fill="none" stroke="var(--brand-red)" stroke-width="1.4"/><ellipse cx="8" cy="8" rx="3" ry="6.5" fill="none" stroke="var(--brand-red)" stroke-width="1.2"/><path d="M1.5 8h13" stroke="var(--brand-red)" stroke-width="1.2"/></svg>www.VantageInspect.com</li>
    </ul>
    <div class="holder-photo" role="img" aria-label="Portrait photo of the inspector in a blue company polo shirt"></div>
    <div class="service-strip">HOME • SEWER • MOLD • COMMERCIAL • TERMITE • ROOF</div>
  </section>

</body>
</html>
```